Wordpress Website design partner needed for an Arabic Language Institute for English Speakers

We are an online Arabic Language institute, targeting English Speakers around the world and we provide online courses and private group and one on one classes
We are looking for a total of 5 pages designed.
The Design should be mobile-first, and then provide PC for any differences.
I am looking for a consistent design with a lot of white space and in line with our Logo colours.
Images used should be around the theme of Arabic Language/Islamic in Nature, so please do not use any illustrations or images of animals or human beings except for silhouettes or images without faces visible, such as someone facing other way or below torso or hands etc.
The website will eventually be prepared for Wordpress using Divi.
I will provide a very structured outline of what elements and modules each page should have. Therefore I am looking for someone that has an eye for detail and is precise in executing requirements.
I decided to post on this site because I am looking for a long-term partner that can take care of any of our design needs as they come up.
More details to follow
I will do abit more research tomorrow to suggest sample sites
Updates
Target Market(s)
English speakers that want to learn Arabic for Religous purposes such as understanding the Quran
Industry/Entity Type
Education
Colors
Designer to choose colors to be used in the design.
Requirements
Must have
- Mobile First, and design for PC for changes
- Consistency
- Plenty of White Space
- Colour Palette based on Logo
- Colour and Transparent/White Header for when scrolling
- Big Call to Action buttons with contrasting colors
- A consistent footer for all pages with
- -Social Media Icons
- -Contact us
- -Sitemap
- -Copyright
- -Logo
- Anything with a hashtag (#) beforehand in the Doc file means it should be a module like the modules used in Divi Theme, Please check the following website for an explanation of what each module consists of and some examples of it in use. https://www.pelmorashowcase.net/pelmora-blocks-guide/
Nice to have
- Parallax Effect
Should not have
- illustrations or images of animals or human beings except for silhouettes or images without faces visible, such as someone facing other way or below torso or hands etc.

```html
<!DOCTYPE html>
<html lang="en">
<head>
<meta charset="utf-8">
<title>Contact Us – Qalam Arabic Academy</title>
<link href="https://fonts.googleapis.com/css2?family=IBM+Plex+Sans:wght@400;500;600;700&display=swap" rel="stylesheet">
<style>
:root{
  --royal:#134b96;
  --royal-deep:#0f3f84;
  --ink:#111;
  --link:#1d4f9c;
  --teal:#2a94a8;
  --line:#d9d9d9;
  --faq-bg:#f4f2f3;
  --footer:#222;
  --white:#fff;
}
*{margin:0;padding:0;box-sizing:border-box}
html,body{width:746px;height:1200px;overflow:hidden}
body{font-family:"IBM Plex Sans",Arial,sans-serif;color:var(--ink);background:var(--white);position:relative}
.abs{position:absolute}

/* hero */
.hero{position:absolute;left:0;top:0;width:746px;height:229px;background:var(--royal);overflow:hidden}
.hero-scene{position:absolute;left:0;top:60px;width:640px;height:169px;
  background:radial-gradient(ellipse 110px 110px at 105px 180px,#1f5cab 0,#1a55a3 70%,transparent 72%),
             radial-gradient(ellipse 400px 60px at 330px 240px,#1c57a6 0,transparent 70%);opacity:.9}
.nav a{position:absolute;top:46px;color:var(--white);font-size:10px;font-weight:500;letter-spacing:.2px;text-decoration:none}
.nav .sep{position:absolute;top:42px;width:1px;height:20px;background:var(--white)}
.nav a.current{color:var(--teal);text-decoration:underline}
.brand{position:absolute;left:334px;top:40px;width:80px;text-align:center;color:var(--white);font-size:13px;font-weight:600;letter-spacing:1px}
.brand .dot{display:block;width:22px;height:22px;border-radius:50%;background:var(--white);margin:0 auto 4px}
.login{position:absolute;left:605px;top:40px;width:58px;height:25px;border:1.5px solid var(--white);border-radius:13px;color:var(--white);font-size:9px;font-weight:500;text-align:center;line-height:22px}
.hero h1{position:absolute;left:0;width:746px;top:140px;text-align:center;color:var(--white);font-size:24px;font-weight:600;letter-spacing:.5px}

/* contact */
.section-title{position:absolute;font-size:14.5px;font-weight:600;letter-spacing:.2px}
.row-label{position:absolute;left:156px;font-size:11px}
.row-value{position:absolute;left:155px;font-size:17px;color:var(--link)}
.vsep{position:absolute;left:141px;width:1px;height:32px;background:var(--line)}
.hr{position:absolute;height:1px;background:var(--line)}
.follow{position:absolute;left:107px;top:467px;font-size:11px}
.soc{position:absolute;top:466px;width:17px;height:17px;border-radius:50%}
.field{position:absolute;left:416px;width:247px;border:1px solid #aaa;border-radius:13px;font-size:8px;padding-left:12px;letter-spacing:.2px}
.submit{position:absolute;left:417px;top:466px;width:77px;height:31px;border-radius:16px;background:var(--teal);color:var(--white);font-size:10.5px;font-weight:600;text-align:center;line-height:31px;letter-spacing:.3px}

/* faq */
.faq{position:absolute;left:0;top:538px;width:746px;height:409px;background:var(--faq-bg)}
.faq h2{position:absolute;top:29px;width:746px;text-align:center;font-size:15px;font-weight:600}
.card{position:absolute;top:78px;width:184px;background:var(--white);box-shadow:0 1px 4px rgba(0,0,0,.06);padding:18px 15px 0 16px}
.card h3{font-size:8.5px;font-weight:600;letter-spacing:.2px;margin-bottom:16px}
.card p{font-size:8.5px;line-height:11px;color:var(--link);font-weight:500;margin:0 0 12px 1px}

/* footer */
.footer{position:absolute;left:0;top:947px;width:746px;height:253px;background:var(--footer);color:var(--white)}
.footer h4{position:absolute;top:36px;font-size:9px;font-weight:500;letter-spacing:.3px}
.f-ic{position:absolute;width:22px;height:22px;border-radius:50%;background:var(--teal)}
.f-small{position:absolute;font-size:8px;line-height:10.5px;font-weight:500}
.f-follow{position:absolute;left:581px;font-size:8.5px;line-height:11px;font-weight:400;letter-spacing:.2px}
.frame{position:absolute;left:267px;top:36px;width:212px;height:105px;border:1px solid #888;border-top:none}
.frame-gap{position:absolute;left:326px;top:139px;width:94px;height:4px;background:var(--footer)}
.f-brand{position:absolute;left:0;width:746px;top:80px;text-align:center;font-size:13px;font-weight:600;letter-spacing:2px}
.f-brand .dot{display:block;width:30px;height:30px;border-radius:50%;background:var(--white);margin:0 auto 8px}
.f-brand small{display:block;font-size:6px;letter-spacing:2px;font-weight:500;margin-top:2px}
.f-links{position:absolute;top:160px;width:746px;text-align:center;font-size:8.5px;font-weight:500;letter-spacing:.2px}
.f-links span{margin:0 5px}
.f-rule{position:absolute;left:81px;top:198px;width:583px;height:1px;background:#555}
.copy{position:absolute;top:223px;width:746px;text-align:center;font-size:7.5px;color:#ddd}
</style>
</head>
<body>

<header class="hero">
  <div class="hero-scene" role="img" aria-label="Blue silhouette of a mosque dome and minarets"></div>
  <nav class="nav">
    <a style="left:196px">HOME</a>
    <span class="sep" style="left:244px"></span>
    <a style="left:262px">ABOUT US</a>
    <a style="left:429px">COURSES</a>
    <span class="sep" style="left:489px"></span>
    <a class="current" style="left:506px">CONTACT US</a>
  </nav>
  <div class="brand"><span class="dot"></span>QALAM</div>
  <div class="login">LOGIN</div>
  <h1>CONTACT US</h1>
</header>

<section class="contact">
  <h2 class="section-title" style="left:99px;top:270px">GET IN TOUCH</h2>
  <svg class="abs" style="left:104px;top:322px" width="24" height="18" viewBox="0 0 24 18" fill="none" stroke="#2a94a8" stroke-width="1.3"><rect x="1" y="1" width="22" height="16"/><path d="M1 1l11 9 11-9M1 17l8-8M23 17l-8-8"/></svg>
  <span class="vsep" style="top:314px"></span>
  <div class="row-label" style="top:313px">E mail us</div>
  <div class="row-value" style="top:330px">info@qalamacademy.com</div>
  <div class="hr" style="left:94px;top:370px;width:233px"></div>

  <svg class="abs" style="left:104px;top:393px" width="24" height="24" viewBox="0 0 24 24" fill="none" stroke="#2a94a8" stroke-width="1.3"><path d="M5 2l4 4-2 3c1 3 4 6 7 7l3-2 4 4-3 3C10 21 3 14 2 5z"/><path d="M14 6a5 5 0 0 1 4 4M14 2a9 9 0 0 1 8 8"/></svg>
  <span class="vsep" style="top:391px"></span>
  <div class="row-label" style="top:386px">Call us</div>
  <div class="row-value" style="top:403px">555.010.0199</div>
  <div class="hr" style="left:94px;top:440px;width:234px"></div>

  <div class="follow">Follow</div>
  <span class="soc" style="left:149px;background:#2b4ea3"></span>
  <span class="soc" style="left:170px;background:#1d9fe0"></span>
  <span class="soc" style="left:192px;background:#142a55"></span>

  <h2 class="section-title" style="left:415px;top:267px">SEND MESSAGE</h2>
  <div class="field" style="top:302px;height:25px;line-height:24px">NAME</div>
  <div class="field" style="top:337px;height:25px;line-height:24px">E MAIL ADDRESS</div>
  <div class="field" style="top:372px;height:77px;border-radius:9px;padding-top:9px">MESSAGE</div>
  <div class="submit">SUBMIT</div>
</section>

<section class="faq">
  <h2>FAQ</h2>
  <div class="card" style="left:81px;height:217px">
    <h3>LOREM IPSUM IS SIMPLY</h3>
    <p>Contrary to popular belief Lorem?</p>
    <p>There are many variations?</p>
    <p>Lorem ipsum dolor sit ametconsec tetur adipiscing elit, sed</p>
    <p>Sed ut perspiciatis unde omnis iste natus lorem psm.</p>
    <p>At vero eos et accusamus et iusto odio dignissimos ducimus qui blanditii lorem ipsum.</p>
  </div>
  <div class="card" style="left:281px;height:295px">
    <h3>LOREM IPSUM IS SIMPLY</h3>
    <p>Contrary to popular belief Lorem?</p>
    <p>There are many variations?</p>
    <p>Lorem ipsum dolor sit ametconsec tetur adipiscing elit, sed</p>
    <p>Sed ut perspiciatis unde omnis iste natus lorem psm.</p>
    <p>At vero eos et accusamus et iusto odio dignissimos ducimus qui blanditii lorem ipsum.</p>
    <p>But I must explain to you how all this mistaken idea of denouncing</p>
    <p>Lorem ipsum dolor sit amet onsect etur adipiscing elit, sed do eius mod tempor</p>
  </div>
  <div class="card" style="left:480px;height:217px">
    <h3>LOREM IPSUM IS SIMPLY</h3>
    <p>Contrary to popular belief Lorem?</p>
    <p>There are many variations?</p>
    <p>Lorem ipsum dolor sit ametconsec tetur adipiscing elit, sed</p>
    <p>Sed ut perspiciatis unde omnis iste natus lorem psm.</p>
    <p>At vero eos et accusamus et iusto odio dignissimos ducimus qui blanditii lorem ipsum.</p>
  </div>
</section>

<footer class="footer">
  <h4 style="left:85px">CONTACT US</h4>
  <span class="f-ic" style="left:82px;top:66px"></span>
  <svg class="abs" style="left:88px;top:72px" width="10" height="10" viewBox="0 0 24 24" fill="#fff"><path d="M5 2l5 5-3 3c1 3 4 6 7 7l3-3 5 5-3 3C9 22 2 15 2 5z"/></svg>
  <div class="f-small" style="left:113px;top:68px">CALL US<br><span style="font-size:9px">555.010.0199</span></div>
  <span class="f-ic" style="left:82px;top:1061px;top:114px"></span>
  <svg class="abs" style="left:88px;top:121px" width="10" height="8" viewBox="0 0 10 8" fill="#fff"><rect width="10" height="8" rx="1"/><path d="M0 1l5 3.5L10 1" stroke="#2a94a8" fill="none"/></svg>
  <div class="f-small" style="left:113px;top:113px">E MAIL US<br><span style="font-size:9px">info@qalamacademy.com</span></div>

  <div class="frame"></div>
  <div class="frame-gap"></div>
  <div class="f-brand" style="top:50px"><span class="dot"></span>QALAM<small>ARABIC ACADEMY</small></div>
  <div class="f-links"><span>HOME</span><span>ABOUT US</span><span>OUR COURSES</span><span>CONTACT US</span></div>

  <h4 style="left:556px">FOLLOW US</h4>
  <span class="f-ic" style="left:555px;top:75px;width:18px;height:18px"></span>
  <div class="f-follow" style="top:73px">Like us on<br>FRIENDLINE</div>
  <span class="f-ic" style="left:555px;top:113px;width:18px;height:18px"></span>
  <div class="f-follow" style="top:111px">Follow us on<br>CHIRPER</div>
  <span class="f-ic" style="left:555px;top:151px;width:18px;height:18px"></span>
  <div class="f-follow" style="top:149px">Follow us on<br>WORKNET</div>

  <div class="f-rule"></div>
  <div class="copy">Copyright © 2020 All Rights Reserved</div>
</footer>

</body>
</html>
```